Maple Roster Business Card for recruitment company

We are looking for a Business Card Design that incorporates our personal details and our busines name and logo. We are a specialized search consultancy that recruit Property and Construction professionals.
We would like a business card that stands out and is appealing to the Construction and Property industry as well.

Target Market(s)

people in the construction and property industry

Contact Information for Business Card

Business Name and logo

Font styles to use
Serif

Colors
0094D4
00A9DD
6FCCEA
C7EBF8
E9F6FB

Requirements
Must have
• Business name and logo as well as contact details
Should not have
• No photos of us please

```html
<!DOCTYPE html>
<html lang="en">
<head>
<meta charset="utf-8">
<title>Maple Roster Business Card</title>
<link href="https://fonts.googleapis.com/css2?family=Lato:wght@300;400;700&display=swap" rel="stylesheet">
<style>
  :root {
    --backdrop: #a3a3a3;
    --paper: #f7f7f6;
    --ink-teal: #1e5569;
    --ink-grey: #7a7a7a;
    --ink-dark: #333333;
  }
  * { margin: 0; padding: 0; box-sizing: border-box; }
  html, body { width: 1200px; height: 1050px; overflow: hidden; }
  body {
    background: var(--backdrop);
    font-family: "Lato", sans-serif;
    position: relative;
  }
  .card {
    position: absolute;
    background: var(--paper);
  }
  .card::before {
    content: "";
    position: absolute;
    inset: 12px;
    border: 1.5px dashed var(--ink-teal);
    pointer-events: none;
  }
  /* Front: portrait layout */
  .card-front {
    left: 110px; top: 170px;
    width: 400px; height: 700px;
    display: flex; flex-direction: column; align-items: center;
    padding-top: 120px;
    text-align: center;
  }
  .brand-lockup {
    display: flex; align-items: center; gap: 12px;
    color: var(--ink-teal);
    font-weight: 700; font-size: 22px; letter-spacing: 2px;
  }
  .brand-dot {
    width: 26px; height: 26px; border-radius: 50%;
    background: var(--ink-teal);
  }
  .person-name {
    margin-top: 44px;
    color: var(--ink-teal);
    font-size: 30px; font-weight: 400; letter-spacing: 0.5px;
  }
  .person-role {
    color: var(--ink-dark);
    font-size: 17px; font-weight: 400;
    margin-top: 2px;
  }
  .divider {
    width: 28px; height: 2px;
    background: var(--ink-teal);
    margin: 22px 0;
  }
  .address {
    color: var(--ink-grey);
    font-size: 18px; font-weight: 300; line-height: 1.4;
  }
  .icon-row {
    display: flex; gap: 6px;
    margin: 26px 0 22px;
  }
  .icon {
    width: 26px; height: 26px; border-radius: 50%;
    background: var(--ink-teal);
    display: flex; align-items: center; justify-content: center;
  }
  .icon svg { width: 14px; height: 14px; }
  .contact-list {
    list-style: none;
    color: var(--ink-grey);
    font-size: 18px; font-weight: 300; line-height: 1.45;
  }
  /* Back: landscape layout */
  .card-back {
    left: 570px; top: 380px;
    width: 540px; height: 310px;
    display: flex; align-items: center; justify-content: center;
  }
  .wordmark {
    color: var(--ink-teal);
    font-size: 50px; font-weight: 400; letter-spacing: 4px;
    white-space: nowrap;
  }
</style>
</head>
<body>
  <section class="card card-front" aria-label="Business card front">
    <div class="brand-lockup">
      <span class="brand-dot"></span>
      <span class="brand-name">MAPLE ROSTER</span>
    </div>
    <h1 class="person-name">DANIEL HART</h1>
    <p class="person-role">President</p>
    <span class="divider"></span>
    <p class="address">412 Alder Court<br>Juneau, Alaska 99801</p>
    <div class="icon-row">
      <span class="icon" aria-label="Phone"><svg viewBox="0 0 14 14"><path d="M3 1.5l2.2 2.4-1.1 1.4c.8 1.7 2 2.9 3.6 3.7l1.4-1.1 2.4 2.2-1.3 1.9C6 11.8 2.2 8 2 3z" fill="#fff"/></svg></span>
      <span class="icon" aria-label="Mobile"><svg viewBox="0 0 14 14"><rect x="4" y="1.5" width="6" height="11" rx="1" fill="none" stroke="#fff" stroke-width="1.4"/></svg></span>
      <span class="icon" aria-label="Fax"><svg viewBox="0 0 14 14"><rect x="2" y="5" width="10" height="6" fill="#fff"/><rect x="4" y="2" width="6" height="3" fill="none" stroke="#fff" stroke-width="1.2"/></svg></span>
      <span class="icon" aria-label="Email"><svg viewBox="0 0 14 14"><rect x="2" y="3.5" width="10" height="7" fill="none" stroke="#fff" stroke-width="1.2"/><path d="M2 3.5l5 4 5-4" fill="none" stroke="#fff" stroke-width="1.2"/></svg></span>
      <span class="icon" aria-label="Website"><svg viewBox="0 0 14 14"><circle cx="7" cy="7" r="5" fill="none" stroke="#fff" stroke-width="1.2"/><path d="M2 7h10M7 2c-2.5 3-2.5 7 0 10M7 2c2.5 3 2.5 7 0 10" fill="none" stroke="#fff" stroke-width="1"/></svg></span>
    </div>
    <ul class="contact-list">
      <li>555-204-7731</li>
      <li>555-318-6402</li>
      <li>555-427-9150</li>
      <li>daniel@mapleroster.com</li>
      <li>www.mapleroster.com</li>
    </ul>
  </section>

  <section class="card card-back" aria-label="Business card back">
    <p class="wordmark">MAPLE ROSTER</p>
  </section>
</body>
</html>
```